Computer consultant business card

Bexil Software is a newly started computer consulting company. It's a small one-man company that provides mostly Vornix applications but also websites in collaboration with designers. I'm running this company on the side of full time university studies.

I want the final design to be clean and memorable. Be creative! :)

Some inspiration:
http://www.pixelmarta.com/design/48317
http://www.pixelmarta.com/design/2739164/business-card-design-by-frostlynk
http://www.pixelmarta.com/design/604281/business-card-design-by-koralind-vestrabanu

See attachment for my company logo.
Updates

I would like to thank everyone for submitting! I'll need a couple of days to review and ultimately select a design.

Target Market(s)

Non-technical entrepreneurs and small companies.

Industry/Entity Type

University

Requirements
Must have
• My company logo.
In any way, both colors from my logo.
First- and last name, e-mail and phone number.
Double-sided design.
Nice to have
• Something creative with the symbol in my logo

```html
<!DOCTYPE html>
<html lang="en">
<head>
<meta charset="utf-8">
<title>Bexil Software — Business Card</title>
<link rel="stylesheet" href="https://fonts.googleapis.com/css2?family=Titillium+Web:wght@300;400;600&display=swap">
<style>
  :root {
    --page-bg: #e9e7e3;
    --brand-blue: #3d6fc6;
    --brand-dark: #2b2b2e;
    --card-light-a: #f7f7f7;
    --card-light-b: #dcdcdd;
    --card-dark-a: #3a3b3e;
    --card-dark-mid: #26272a;
    --card-dark-b: #17181a;
    --emboss: #3b3c40;
    --text-muted: #3a3a3c;
    --facet: rgba(255, 255, 255, 0.55);
  }
  html, body {
    margin: 0;
    padding: 0;
    width: 1200px;
    height: 1024px;
    overflow: hidden;
    background: var(--page-bg);
    font-family: "Titillium Web", Arial, sans-serif;
  }
  .canvas {
    position: relative;
    width: 1200px;
    height: 1024px;
  }
  .card {
    position: absolute;
    left: 290px;
    width: 620px;
    height: 354px;
    border-radius: 4px;
    overflow: hidden;
    box-shadow: 0 10px 30px rgba(0, 0, 0, 0.18);
  }
  .card--front {
    top: 120px;
    background: linear-gradient(135deg, var(--card-light-a) 0%, #ececec 45%, var(--card-light-b) 100%);
  }
  .card--back {
    top: 550px;
    background: var(--card-dark-b);
  }
  .front-facets {
    position: absolute;
    inset: 0;
  }
  .brand {
    position: absolute;
    left: 58px;
    top: 200px;
    display: flex;
    align-items: center;
    gap: 14px;
  }
  .brand__dot {
    width: 46px;
    height: 46px;
    border-radius: 50%;
    background: var(--brand-blue);
  }
  .brand__name {
    font-size: 58px;
    font-weight: 600;
    line-height: 1;
    color: var(--brand-dark);
    letter-spacing: 0.5px;
  }
  .divider {
    position: absolute;
    left: 318px;
    top: 58px;
    width: 1px;
    height: 132px;
    background: var(--brand-blue);
  }
  .info {
    position: absolute;
    left: 340px;
    top: 50px;
  }
  .info__name {
    margin: 0;
    font-size: 30px;
    font-weight: 400;
    letter-spacing: 1.5px;
    color: var(--brand-blue);
    line-height: 1.1;
  }
  .info__title {
    margin: 2px 0 22px;
    font-size: 14px;
    font-weight: 400;
    color: var(--text-muted);
  }
  .contact {
    list-style: none;
    margin: 0;
    padding: 0;
  }
  .contact__item {
    display: flex;
    align-items: center;
    gap: 10px;
    font-size: 15px;
    font-weight: 300;
    color: var(--text-muted);
    line-height: 26px;
  }
  .contact__icon {
    width: 14px;
    height: 14px;
    flex: none;
  }
  .back-pattern {
    position: absolute;
    inset: 0;
    background:
      radial-gradient(ellipse at 40% 35%, var(--card-dark-a) 0%, var(--card-dark-mid) 55%, var(--card-dark-b) 100%);
  }
  .back-sheen {
    position: absolute;
    inset: 0;
    background: linear-gradient(160deg, rgba(255,255,255,0.06) 0%, rgba(255,255,255,0) 45%);
  }
  .back-brand {
    position: absolute;
    left: 150px;
    top: 96px;
    display: flex;
    align-items: center;
    gap: 30px;
  }
  .back-brand__dot {
    width: 150px;
    height: 150px;
    border-radius: 50%;
    background: var(--emboss);
  }
  .back-brand__name {
    font-size: 120px;
    font-weight: 600;
    line-height: 1;
    color: var(--emboss);
    letter-spacing: 1px;
  }
</style>
</head>
<body>
<main class="canvas">

  <section class="card card--front" aria-label="Business card front">
    <svg class="front-facets" viewBox="0 0 620 354" aria-hidden="true">
      <polygon points="0,0 260,0 0,210" fill="var(--facet)" opacity="0.35"/>
      <polygon points="620,0 620,140 380,354 240,354" fill="#ffffff" opacity="0.18"/>
      <line x1="0" y1="300" x2="620" y2="90" stroke="#ffffff" stroke-width="1" opacity="0.6"/>
    </svg>

    <div class="brand">
      <span class="brand__dot"></span>
      <span class="brand__name">bexil</span>
    </div>

    <div class="divider"></div>

    <div class="info">
      <h1 class="info__name">TOMAS VELL</h1>
      <p class="info__title">Managing Director</p>
      <ul class="contact">
        <li class="contact__item">
          <svg class="contact__icon" viewBox="0 0 14 14" aria-hidden="true">
            <rect width="14" height="14" rx="2" fill="var(--brand-blue)"/>
            <rect x="4" y="2.5" width="6" height="9" rx="1" fill="none" stroke="#fff" stroke-width="1.2"/>
            <line x1="6" y1="9.8" x2="8" y2="9.8" stroke="#fff" stroke-width="1"/>
          </svg>
          + (00) 1 98 765 4321
        </li>
        <li class="contact__item">
          <svg class="contact__icon" viewBox="0 0 14 14" aria-hidden="true">
            <rect width="14" height="14" rx="2" fill="var(--brand-blue)"/>
            <rect x="2.5" y="4" width="9" height="6.5" fill="none" stroke="#fff" stroke-width="1.1"/>
            <polyline points="2.5,4 7,8 11.5,4" fill="none" stroke="#fff" stroke-width="1.1"/>
          </svg>
          tomas@bexil.com.au
        </li>
      </ul>
    </div>
  </section>

  <section class="card card--back" aria-label="Business card back">
    <div class="back-pattern" role="img" aria-label="Dark charcoal background with a repeating tonal pattern of rounded brand shapes"></div>
    <div class="back-sheen" aria-hidden="true"></div>
    <div class="back-brand">
      <span class="back-brand__dot"></span>
      <span class="back-brand__name">bexil</span>
    </div>
  </section>

</main>
</body>
</html>
```